KTWG application splash screen

We need a 1024x768 image for use as an application splash screen.
The image will be displayed full screen on an 10 inch industrial PC 1024x768 screen while our application is launching. The image should convey that the application is "Waiting for connection to Wi-Fi access point..." and include a graphic of the industrial PC connected to the access point via an Ethernet cable. A list of troubleshooting steps should be included at the bottom of the image. The troubleshooting steps should not be the main focus of the image and should be shown in a smaller font (but still readable at 1024x768 displayed on a 10 inch screen).
I will include a mock up of the general idea of what we are looking for as well as image files for the industrial PC, a screenshot of our application to show on the PC's screen and the AP.
For general look and feel and a sense of corporate branding please review our website https://marrowgatesoilworks.example/. The splash screen should reflect corporate branding.
Target Market(s)
Users of our application
Industry/Entity Type
Agriculture
Look and feel

```html
<!DOCTYPE html>
<html lang="en">
<head>
<meta charset="utf-8">
<title>KTWG – Waiting for Wi-Fi access point</title>
<link href="https://fonts.googleapis.com/css2?family=Lexend:wght@600;700&family=Poppins:wght@500&family=Oswald:wght@400;600&display=swap" rel="stylesheet">
<style>
  :root {
    --green: #2db56e;
    --green-band: #2fb672;
    --ink: #1f1f22;
    --label: #2b2b2e;
    --white: #ffffff;
    --device-dark: #3a3d42;
    --device-screen: #e9eef0;
    --ap-body: #eef0f2;
  }
  * { margin: 0; padding: 0; box-sizing: border-box; }
  html, body { width: 1200px; height: 900px; overflow: hidden; background: var(--white); }
  .splash { position: relative; width: 1200px; height: 900px; background: var(--white); overflow: hidden; }
  .top-rule { position: absolute; left: 0; top: 0; width: 1200px; height: 5px; background: var(--ink); }

  .brand { position: absolute; left: 46px; top: 44px; display: flex; align-items: center; gap: 14px; }
  .brand-dot { width: 34px; height: 34px; border-radius: 50%; background: var(--green); }
  .brand-name { font-family: "Lexend", sans-serif; font-weight: 700; font-size: 58px; letter-spacing: 2px; color: var(--ink); line-height: 1; }

  .status-title {
    position: absolute; left: 383px; top: 72px; width: 600px;
    font-family: "Lexend", sans-serif; font-weight: 700; font-size: 61px; line-height: 84px;
    color: var(--green); text-align: center; letter-spacing: -0.5px;
  }

  .device { position: absolute; border-radius: 10px; }
  .cab-computer { left: 56px; top: 346px; width: 278px; height: 214px; background: linear-gradient(180deg, var(--device-dark), #25272b); }
  .cab-computer .screen { position: absolute; left: 16px; top: 20px; width: 246px; height: 156px; background: var(--device-screen); border-radius: 2px; }
  .access-point { left: 1049px; top: 246px; width: 48px; height: 246px; background: linear-gradient(90deg, #dfe2e5, var(--ap-body), #d6d9dc); border-radius: 8px; }

  .link-diagram { position: absolute; left: 0; top: 0; }

  .caption { position: absolute; font-family: "Poppins", sans-serif; font-weight: 500; font-size: 20px; color: var(--label); white-space: nowrap; transform: translateX(-50%); }
  .caption-computer { left: 191px; top: 575px; }
  .caption-cable { left: 683px; top: 486px; }
  .caption-ap { left: 1064px; top: 544px; }

  .footer-shape { position: absolute; left: 0; top: 630px; }

  .troubleshoot-heading {
    position: absolute; left: 176px; top: 765px;
    font-family: "Oswald", sans-serif; font-weight: 600; font-size: 27px; color: var(--white);
  }
  .troubleshoot-list {
    position: absolute; left: 500px; top: 713px; list-style: none;
    font-family: "Oswald", sans-serif; font-weight: 400; font-size: 15.5px; line-height: 25px; color: var(--white);
  }
  .troubleshoot-list li::before { content: "• "; }
  .troubleshoot-list .sub { list-style: none; margin-left: 52px; }
  .troubleshoot-list .sub li { padding-left: 14px; text-indent: -14px; width: 470px; }
  .troubleshoot-list .sub li::before { content: "◦ "; }
</style>
</head>
<body>
<main class="splash">
  <div class="top-rule"></div>

  <div class="brand">
    <span class="brand-dot"></span>
    <span class="brand-name">KTWG</span>
  </div>

  <h1 class="status-title">Waiting for<br>connection to<br>Wi-Fi access point...</h1>

  <svg class="link-diagram" width="1200" height="640" viewBox="0 0 1200 640">
    <path d="M340 530 H1073 V494" fill="none" stroke="var(--ink)" stroke-width="3"/>
    <rect x="334" y="523" width="18" height="14" rx="2" fill="var(--ink)"/>
    <rect x="1066" y="494" width="14" height="16" rx="2" fill="var(--ink)"/>
  </svg>

  <div class="device cab-computer" role="img" aria-label="Rugged tractor cab tablet computer showing the seeding application screen">
    <div class="screen"></div>
  </div>
  <div class="device access-point" role="img" aria-label="Outdoor Wi-Fi access point with two antennas"></div>

  <p class="caption caption-computer">Tractor cab computer</p>
  <p class="caption caption-cable">Ethernet cable</p>
  <p class="caption caption-ap">Wi-Fi Access Point</p>

  <svg class="footer-shape" width="1200" height="270" viewBox="0 0 1200 270">
    <polygon points="0,50 603,8 1200,50 1200,60 603,18 0,60" fill="var(--ink)"/>
    <polygon points="0,56 603,14 1200,56 1200,270 0,270" fill="var(--green-band)"/>
  </svg>

  <h2 class="troubleshoot-heading">Troubleshooting steps:</h2>
  <ul class="troubleshoot-list">
    <li>This screen should only be visible for a short time on boot.</li>
    <li>If this screen stays visible for more than a minute:
      <ul class="sub">
        <li>Verify that when the cab computer is powered up the Wi-Fi Access Point (AP) is also powered up (indicated by green light on side of the AP).</li>
        <li>Check the Ethernet cable for damage and replace if damaged.</li>
        <li>Contact KTWG support for further assistance.</li>
      </ul>
    </li>
  </ul>
</main>
</body>
</html>
```